Dultavo.com webside

I want to build a Dultavo.com retail website use on Shopify, reselling three main categories: Office Supplies, Packing Supplies, and Home Consumables. I also wish the webpage has the same functions as the Zelvik home page. The page is split into three different parts with the top being a sliding screen showcasing promotion products, below it being the three categories, and finally, a moving screen showing company missions.
Target Market(s)
U.S online
Industry/Entity Type
Office Supplies, packing Supplies and Home Consumables
Coding
Coded - Design and coding required
Number of Pages Required
5+ page
Look and feel

```html
<!DOCTYPE html>
<html lang="en">
<head>
<meta charset="utf-8">
<title>Dultavo – Office, Packing &amp; Home Supplies</title>
<link href="https://fonts.googleapis.com/css2?family=Poppins:wght@400;500;600;700;800&family=Roboto:wght@400;500;700&display=swap" rel="stylesheet">
<style>
:root{
  --teal:#14b29a;
  --teal-dark:#0e9c86;
  --ink:#111111;
  --text:#333333;
  --muted:#666666;
  --light:#f5f5f5;
  --footer:#1f1f1f;
  --white:#ffffff;
  --star:#f5a623;
}
*{box-sizing:border-box;margin:0;padding:0}
html,body{width:1200px;height:3676px;overflow:hidden}
body{font-family:'Roboto',sans-serif;color:var(--text);background:var(--white);position:relative}
.topbar{height:36px;background:var(--teal);color:var(--white);font-size:14px;display:flex;align-items:center;justify-content:center}
.header{height:108px;display:flex;align-items:center;padding:0 112px;justify-content:space-between}
.logo{font-family:'Poppins',sans-serif;font-weight:700;font-size:40px;color:var(--ink)}
.nav{display:flex;align-items:center;gap:26px;font-size:14px;font-family:'Poppins',sans-serif;font-weight:500;color:var(--ink)}
.nav .active{color:var(--teal)}
.nav svg{display:block}
.cart{position:relative}
.cart .badge{position:absolute;top:-8px;right:-9px;background:var(--teal);color:#fff;border-radius:50%;width:14px;height:14px;font-size:9px;display:flex;align-items:center;justify-content:center}
.btn{display:inline-flex;align-items:center;gap:10px;background:var(--teal);color:var(--white);font-family:'Poppins',sans-serif;font-weight:600;font-size:14px;padding:12px 28px;border-radius:3px}
.btn-login{padding:12px 34px;margin-left:20px}
.hero{position:relative;height:676px;background:linear-gradient(100deg,#6f655c 0%,#a89c8f 28%,#8fa9b8 50%,#3d9ccf 62%,#b9c6cc 78%,#e6e1da 100%);overflow:hidden}
.hero-text{position:absolute;left:112px;top:176px}
.hero-special{font-family:'Poppins',sans-serif;font-weight:600;font-size:44px;color:var(--teal)}
.hero-big{font-family:'Poppins',sans-serif;font-weight:700;font-size:96px;color:var(--white);line-height:1}
.hero-off{font-family:'Poppins',sans-serif;font-weight:700;font-size:44px;color:var(--teal);margin-top:6px}
.hero .btn{position:absolute;left:112px;top:440px;padding:16px 30px}
.arrow{position:absolute;top:320px;width:36px;height:36px;border-radius:50%;background:var(--white);display:flex;align-items:center;justify-content:center}
.arrow.left{left:40px}.arrow.right{right:40px}
.section-title{font-family:'Poppins',sans-serif;font-weight:700;font-size:38px;color:var(--ink);text-align:center}
.section-title::after{content:"";display:block;width:60px;height:4px;background:var(--teal);margin:12px auto 0}
.products{position:absolute;top:880px;left:0;width:1200px}
.product-row{position:absolute;top:108px;left:112px;display:flex;gap:34px}
.product{width:220px;text-align:center}
.product-img{height:220px;border:1px solid #ececec;position:relative}
.tag{position:absolute;top:8px;left:8px;background:var(--teal);color:#fff;font-size:11px;padding:3px 8px;border-radius:3px}
.quick{position:absolute;left:30px;right:30px;bottom:40px;background:var(--teal);color:#fff;font-size:13px;font-weight:500;padding:9px 0}
.price{color:var(--teal);font-size:14px;margin-top:14px}
.product-title{font-family:'Poppins',sans-serif;font-weight:600;font-size:17px;color:var(--ink);margin-top:8px}
.add{color:var(--teal);font-size:14px;margin-top:8px;display:flex;align-items:center;justify-content:center;gap:8px}
.mission{position:absolute;top:1416px;left:0;width:1200px;height:444px;background:linear-gradient(90deg,#0fae96,#3cc5ad 60%,#21b79f);color:var(--white);text-align:center}
.mission .section-title{color:var(--white);margin-top:78px}
.mission .section-title::after{background:var(--white)}
.mission p{width:940px;margin:26px auto 0;font-size:14.5px;line-height:1.55}
.mission .btn{background:var(--teal-dark);margin-top:32px}
.category{position:absolute;top:1940px;left:0;width:1200px}
.cat-row{position:absolute;top:88px;left:112px;display:flex;gap:24px}
.cat{width:308px;text-align:center}
.cat-img{height:220px}
.cat-name{font-family:'Poppins',sans-serif;font-weight:600;font-size:14px;color:var(--ink);margin-top:22px}
.about{position:absolute;top:2380px;left:0;width:1200px;height:480px}
.about-text{position:absolute;left:0;top:0;width:600px;height:480px;background:var(--teal);color:var(--white);padding:64px 112px 0 112px}
.about-text h2{font-family:'Poppins',sans-serif;font-weight:700;font-size:40px;line-height:1.3}
.about-text h2::after{content:"";display:block;width:60px;height:4px;background:var(--white);margin-top:10px}
.about-text p{font-size:14.5px;line-height:1.5;margin-top:20px}
.about-text .btn{background:var(--teal-dark);margin-top:24px}
.about-img{position:absolute;left:600px;top:0;width:600px;height:480px;background:linear-gradient(180deg,#eceae6 0%,#d9d5cf 55%,#b58a5e 80%,#8a6a4c 100%)}
.reviews{position:absolute;top:2980px;left:0;width:1200px}
.review-row{position:absolute;top:104px;left:96px;display:flex;gap:28px}
.review{width:320px;height:204px;background:var(--light);text-align:center;padding:22px 26px 0}
.stars{color:var(--star);font-size:16px;letter-spacing:3px}
.review p{font-size:14.5px;line-height:1.45;margin-top:10px;color:var(--text)}
.avatar{width:46px;height:46px;border-radius:50%;background:#8a9aa8;margin:14px auto 0}
.review-name{font-family:'Poppins',sans-serif;font-weight:600;font-size:13px;color:var(--ink);margin-top:4px}
.footer{position:absolute;top:3408px;left:0;width:1200px;height:268px;background:var(--footer);color:var(--white)}
.footer h4{font-family:'Poppins',sans-serif;font-weight:600;font-size:16px}
.f-links{position:absolute;left:112px;top:36px}
.f-links ul{list-style:none;margin-top:22px;font-size:15px;line-height:1.85}
.f-social{position:absolute;left:380px;top:36px}
.socials{display:flex;gap:12px;margin-top:20px}
.socials span{width:32px;height:32px;border:1.5px solid var(--white);border-radius:50%}
.f-news{position:absolute;left:724px;top:36px;width:364px}
.f-input{margin-top:32px;border-bottom:1px solid #777;display:flex;justify-content:space-between;padding-bottom:10px;font-size:14px;color:#ccc}
.copyright{position:absolute;left:724px;top:152px;font-size:14px;color:#ddd}
</style>
</head>
<body>
<div class="topbar">Free Shipping On Orders Over $50</div>
<header class="header">
  <div class="logo">Dultavo</div>
  <nav class="nav">
    <span class="active">HOME</span><span>MISSION</span><span>PRODUCTS</span><span>CATEGORY</span><span>CONTACT US</span>
    <svg width="16" height="16" viewBox="0 0 16 16"><circle cx="7" cy="7" r="5" fill="none" stroke="#111" stroke-width="2"/><line x1="11" y1="11" x2="15" y2="15" stroke="#111" stroke-width="2"/></svg>
    <span class="cart"><svg width="18" height="16" viewBox="0 0 18 16"><path d="M1 1h3l2 9h9l2-7H5" fill="none" stroke="#111" stroke-width="1.8"/><circle cx="7" cy="14" r="1.5" fill="#111"/><circle cx="14" cy="14" r="1.5" fill="#111"/></svg><span class="badge">0</span></span>
    <span class="btn btn-login">LOGIN <svg width="12" height="12" viewBox="0 0 12 12"><circle cx="6" cy="3.5" r="3" fill="#fff"/><path d="M0 12c0-4 12-4 12 0z" fill="#fff"/></svg></span>
  </nav>
</header>

<section class="hero" role="img" aria-label="Cleaning bucket with sprays, brushes and gloves on a living room table">
  <div class="hero-text">
    <div class="hero-special">Special Offer</div>
    <div class="hero-big">Big Sale</div>
    <div class="hero-off">Up To 75% Off</div>
  </div>
  <span class="btn">SHOP NOW <svg width="14" height="12" viewBox="0 0 18 16"><path d="M1 1h3l2 9h9l2-7H5" fill="none" stroke="#fff" stroke-width="2"/><circle cx="7" cy="14" r="1.5" fill="#fff"/><circle cx="14" cy="14" r="1.5" fill="#fff"/></svg></span>
  <span class="arrow left"><svg width="10" height="12" viewBox="0 0 10 12"><path d="M8 1L2 6l6 5" fill="none" stroke="#111" stroke-width="2"/></svg></span>
  <span class="arrow right"><svg width="10" height="12" viewBox="0 0 10 12"><path d="M2 1l6 5-6 5" fill="none" stroke="#111" stroke-width="2"/></svg></span>
</section>

<section class="products">
  <h2 class="section-title">Our Products</h2>
  <div class="product-row">
    <div class="product"><div class="product-img" role="img" aria-label="Hand sanitizer pump bottle" style="background:linear-gradient(180deg,#ffffff,#d9ecf8)"></div><div class="price">$5.00</div><div class="product-title">Products Tittle</div><div class="add">Add to cart <svg width="14" height="12" viewBox="0 0 18 16"><path d="M1 1h3l2 9h9l2-7H5" fill="none" stroke="#14b29a" stroke-width="2"/></svg></div></div>
    <div class="product"><div class="product-img" role="img" aria-label="Cup of colored pens and pencils" style="background:linear-gradient(180deg,#ffffff,#f6dede)"><span class="tag">New</span><span class="quick">Quick View</span></div><div class="price">$5.00</div><div class="product-title">Products Tittle</div><div class="add">Add to cart <svg width="14" height="12" viewBox="0 0 18 16"><path d="M1 1h3l2 9h9l2-7H5" fill="none" stroke="#14b29a" stroke-width="2"/></svg></div></div>
    <div class="product"><div class="product-img" role="img" aria-label="Roll of clear packing tape" style="background:linear-gradient(180deg,#ffffff,#f1ead9)"></div><div class="price">$5.00</div><div class="product-title">Products Tittle</div><div class="add">Add to cart <svg width="14" height="12" viewBox="0 0 18 16"><path d="M1 1h3l2 9h9l2-7H5" fill="none" stroke="#14b29a" stroke-width="2"/></svg></div></div>
    <div class="product"><div class="product-img" role="img" aria-label="Red desktop stapler" style="background:linear-gradient(180deg,#ffffff,#f5d9d7)"></div><div class="price">$5.00</div><div class="product-title">Products Tittle</div><div class="add">Add to cart <svg width="14" height="12" viewBox="0 0 18 16"><path d="M1 1h3l2 9h9l2-7H5" fill="none" stroke="#14b29a" stroke-width="2"/></svg></div></div>
  </div>
</section>

<section class="mission">
  <h2 class="section-title">Our Mission</h2>
  <p>Lorem ipsum dolor sit amet, consectetur adipiscing elit, sed do eiusmod tempor incididunt ut labore et dolore magna aliqua. Ut enim ad minim veniam, quis nostrud exercitation ullamco laboris nisi ut aliquip ex ea commodo consequat. Duis aute irure dolor in reprehenderit in voluptate velit esse cillum dolore eu fugiat nulla pariatur. Excepteur sint occaecat cupidatat non proident, sunt in culpa qui officia deserunt mollit anim id est laborum lorem ipsum dolor sit amet, consectetur adipiscing elit, sed do eiusmod tempor incididunt ut labore et dolore magna aliqua minim veniam nostrud exercitation ullamco laboris.</p>
  <span class="btn">LEARN MORE <svg width="12" height="12" viewBox="0 0 12 12"><circle cx="6" cy="6" r="6" fill="#fff"/><path d="M5 3.5L7.5 6 5 8.5" fill="none" stroke="#0e9c86" stroke-width="1.6"/></svg></span>
</section>

<section class="category">
  <h2 class="section-title">Our Category</h2>
  <div class="cat-row">
    <div class="cat"><div class="cat-img" role="img" aria-label="Desk with office supplies and organizers" style="background:linear-gradient(135deg,#5a3b26,#a9744a 45%,#d8c6b0)"></div><div class="cat-name">Office Supplies</div></div>
    <div class="cat"><div class="cat-img" role="img" aria-label="Hands taping a cardboard box" style="background:linear-gradient(135deg,#b98c5c,#d9b383 50%,#c8d34a)"></div><div class="cat-name">Packing Supplies</div></div>
    <div class="cat"><div class="cat-img" role="img" aria-label="Basket of household cleaning products" style="background:linear-gradient(135deg,#7b8794,#b9c3cc 50%,#5f8fb8)"></div><div class="cat-name">Home Consumables</div></div>
  </div>
</section>

<section class="about">
  <div class="about-text">
    <h2>About Us</h2>
    <p>Lorem ipsum dolor sit amet, consectetur adipiscing elit, sed do eiusmod tempor incididunt ut labore et dolore magna aliqua. Ut enim ad minim veniam, quis nostrud exercitation ullamco laboris nisi ut aliquip ex ea commodo consequat. Duis aute irure dolor in reprehenderit in voluptate velit esse cillum dolore eu fugiat nulla pariatur. Excepteur sint occaecat cupidatat non proident, sunt in culpa qui officia deserunt mollit anim id est laborum sed do eiusmod tempor.</p>
    <span class="btn">LEARN MORE <svg width="12" height="12" viewBox="0 0 12 12"><circle cx="6" cy="6" r="6" fill="#fff"/><path d="M5 3.5L7.5 6 5 8.5" fill="none" stroke="#0e9c86" stroke-width="1.6"/></svg></span>
  </div>
  <div class="about-img" role="img" aria-label="Bright office with wooden desk, leather chairs and pendant lamps"></div>
</section>

<section class="reviews">
  <h2 class="section-title">Customer Reviews</h2>
  <div class="review-row">
    <div class="review"><div class="stars">★★★★★</div><p>Lorem ipsum dolor sited consectetur adipiscing elit, sed do eiusmod tempor incididunt ute labore eted dolorel.</p><div class="avatar" role="img" aria-label="Customer portrait"></div><div class="review-name">Jhon deo</div></div>
    <div class="review"><div class="stars">★★★★★</div><p>Lorem ipsum dolor sited consectetur adipiscing elit, sed do eiusmod tempor incididunt ute labore eted dolorel.</p><div class="avatar" role="img" aria-label="Customer portrait"></div><div class="review-name">Jhon deo</div></div>
    <div class="review"><div class="stars">★★★★★</div><p>Lorem ipsum dolor sited consectetur adipiscing elit, sed do eiusmod tempor incididunt ute labore eted dolorel.</p><div class="avatar" role="img" aria-label="Customer portrait"></div><div class="review-name">Jhon deo</div></div>
  </div>
</section>

<footer class="footer">
  <div class="f-links"><h4>Quick links</h4><ul><li>Home</li><li>Mission</li><li>Products</li><li>category</li><li>Contact Us</li></ul></div>
  <div class="f-social"><h4>Follow us</h4><div class="socials"><span></span><span></span><span></span><span></span></div></div>
  <div class="f-news"><h4>Join Our Newsletter</h4><div class="f-input">Enter email <svg width="16" height="12" viewBox="0 0 16 12"><rect x="1" y="1" width="14" height="10" fill="none" stroke="#fff" stroke-width="1.5"/><path d="M1 1l7 6 7-6" fill="none" stroke="#fff" stroke-width="1.5"/></svg></div></div>
  <div class="copyright">© 2022 Dultavo All Rights Reserved.</div>
</footer>
</body>
</html>
```